Bookmark Design

We would like to design a book mark with logos of our two business and a quote.

One side with the quote "The first wealth is health" - Tobias Kendrick Mallory and the two logos.

The back side has the two logos with its respective phone numbers and a common address (this is to be advised to the winner of the project).

```html
<!DOCTYPE html>
<html lang="en">
<head>
<meta charset="utf-8">
<title>Bookmark – Harbourline Dental &amp; Kelvale Clinic</title>
<link rel="stylesheet" href="https://fonts.googleapis.com/css2?family=Oswald:wght@400;700&family=Yellowtail&family=Ubuntu:wght@500;700&display=swap">
<style>
  :root{
    --page:#ffffff;
    --green:#5fae4a;
    --green-light:#8fcf6e;
    --green-deep:#3f8f3a;
    --blue:#1d55a5;
    --ink:#4a4f5a;
    --silver-top:#d9deea;
    --silver:#9ea5c0;
    --steel:#a3b6c8;
    --ice:#e2f1f8;
    --rule:#b9bcc4;
    --white:#ffffff;
  }
  *{margin:0;padding:0;box-sizing:border-box}
  html,body{width:1200px;height:849px;overflow:hidden;background:var(--page)}
  .canvas{position:relative;width:1200px;height:849px}
  .bookmark{position:absolute;top:116px;width:206px;height:613px}
  .bookmark--front{left:312px}
  .bookmark--back{left:675px}
  .bookmark__shape{position:absolute;left:0;top:0;overflow:visible}
  .bookmark__content{position:absolute;inset:0;text-align:center}
  .abs{position:absolute;left:0;right:0}

  .divider{display:flex;justify-content:center;align-items:center;gap:6px;height:6px}
  .divider span{width:4px;height:4px;border-radius:50%;background:var(--white)}
  .divider span.dash{width:5px;height:1px;border-radius:0}

  .quote__caps{font-family:"Oswald",sans-serif;font-weight:700;color:var(--white);
    letter-spacing:.5px;text-shadow:0 1px 0 #7f86a3, 0 0 1px #6b7394}
  .quote__first{top:101px;font-size:25px;line-height:30px}
  .quote__is{top:189px;font-size:22px;line-height:28px}
  .quote__script{font-family:"Yellowtail",cursive;font-size:52px;line-height:56px;
    color:var(--green-light);text-shadow:1px 1px 0 var(--green-deep), 2px 3px 2px rgba(60,70,90,.35)}
  .quote__wealth{top:129px}
  .quote__health{top:218px}
  .quote__author{top:298px;font-family:"Oswald",sans-serif;font-weight:400;font-size:11px;
    color:var(--white);letter-spacing:.1px}

  .brand{font-family:"Ubuntu",sans-serif;font-weight:700;line-height:1.05}
  .brand--dental{color:var(--green);font-size:21px}
  .brand--clinic{color:var(--blue);font-size:21px}
  .brand__mark{display:block;margin:0 auto 8px;width:38px;height:38px;border-radius:50%;
    border:3px solid var(--blue)}

  .contact{font-family:"Ubuntu",sans-serif;font-weight:700;color:var(--ink);font-size:11px}
  .contact__phone{width:126px;margin:0 auto;padding-bottom:3px;border-bottom:1px dashed var(--rule)}
  .contact__address{font-weight:500;line-height:14px}
  .contact__address strong{font-weight:700}
</style>
</head>
<body>
<main class="canvas">

  <!-- Front side -->
  <section class="bookmark bookmark--front" aria-label="Bookmark front">
    <svg class="bookmark__shape" width="212" height="618" viewBox="0 0 212 618" aria-hidden="true">
      <defs>
        <linearGradient id="frontFill" x1="0" y1="0" x2="0" y2="1">
          <stop offset="0" stop-color="#e3eef6"/>
          <stop offset=".06" stop-color="#c9cede"/>
          <stop offset=".15" stop-color="#9ea5c0"/>
          <stop offset=".35" stop-color="#a3b6c8"/>
          <stop offset=".5" stop-color="#bccad8"/>
          <stop offset=".6" stop-color="#e2f1f8"/>
          <stop offset=".9" stop-color="#dcedf2"/>
          <stop offset="1" stop-color="#cfd3e0"/>
        </linearGradient>
      </defs>
      <path d="M4 83 Q4 69 16 61 L98 8 Q107 3 116 8 L198 61 Q210 69 210 83 L210 602 Q210 616 196 616 L18 616 Q4 616 4 602 Z" fill="#e9eaee"/>
      <path d="M0 80 Q0 66 12 58 L94 5 Q103 0 112 5 L194 58 Q206 66 206 80 L206 599 Q206 613 192 613 L14 613 Q0 613 0 599 Z" fill="url(#frontFill)"/>
      <path d="M8 84 Q8 72 18 65 L96 14 Q103 10 110 14 L188 65 Q198 72 198 84 L198 593 Q198 605 186 605 L20 605 Q8 605 8 593 Z" fill="none" stroke="#fff" stroke-width="1" stroke-dasharray="2 2"/>
      <circle cx="103" cy="32" r="7" fill="#fff" stroke="#c3c8d6" stroke-width="1"/>
    </svg>
    <div class="bookmark__content">
      <div class="abs divider" style="top:79px"><span class="dash"></span><span></span><span></span><span></span><span class="dash"></span></div>
      <p class="abs quote__caps quote__first">THE FIRST</p>
      <p class="abs quote__script quote__wealth">Wealth</p>
      <p class="abs quote__caps quote__is">IS</p>
      <p class="abs quote__script quote__health">Health</p>
      <p class="abs quote__author">- TOBIAS KENDRICK MALLORY -</p>
      <div class="abs divider" style="top:336px"><span class="dash"></span><span></span><span></span><span></span><span class="dash"></span></div>
      <p class="abs brand brand--dental" style="top:392px">Harbourline Dental<br>Kelvale</p>
      <div class="abs brand brand--clinic" style="top:478px"><span class="brand__mark"></span>Kelvale Clinic</div>
    </div>
  </section>

  <!-- Back side -->
  <section class="bookmark bookmark--back" aria-label="Bookmark back">
    <svg class="bookmark__shape" width="212" height="618" viewBox="0 0 212 618" aria-hidden="true">
      <defs>
        <linearGradient id="backFill" x1="0" y1="0" x2="0" y2="1">
          <stop offset="0" stop-color="#e3eef6"/>
          <stop offset=".06" stop-color="#c9cede"/>
          <stop offset=".15" stop-color="#9ea5c0"/>
          <stop offset=".4" stop-color="#a3b6c8"/>
          <stop offset=".62" stop-color="#e2f1f8"/>
          <stop offset=".9" stop-color="#dcedf2"/>
          <stop offset="1" stop-color="#cfd3e0"/>
        </linearGradient>
        <linearGradient id="backBand" x1="0" y1="0" x2="0" y2="1">
          <stop offset="0" stop-color="#aeb3c8"/>
          <stop offset=".05" stop-color="#b9bed0"/>
          <stop offset=".17" stop-color="#ffffff"/>
          <stop offset=".48" stop-color="#ffffff"/>
          <stop offset=".62" stop-color="#d2e2ec"/>
          <stop offset=".72" stop-color="#e6f3f7"/>
          <stop offset=".82" stop-color="#ffffff"/>
          <stop offset=".92" stop-color="#f3f8fa"/>
          <stop offset="1" stop-color="#d8dde6"/>
        </linearGradient>
      </defs>
      <path d="M4 83 Q4 69 16 61 L98 8 Q107 3 116 8 L198 61 Q210 69 210 83 L210 602 Q210 616 196 616 L18 616 Q4 616 4 602 Z" fill="#e9eaee"/>
      <path d="M0 80 Q0 66 12 58 L94 5 Q103 0 112 5 L194 58 Q206 66 206 80 L206 599 Q206 613 192 613 L14 613 Q0 613 0 599 Z" fill="url(#backFill)"/>
      <rect x="20" y="66" width="166" height="530" fill="url(#backBand)"/>
      <path d="M8 84 Q8 72 18 65 L96 14 Q103 10 110 14 L188 65 Q198 72 198 84 L198 593 Q198 605 186 605 L20 605 Q8 605 8 593 Z" fill="none" stroke="#fff" stroke-width="1" stroke-dasharray="2 2"/>
      <circle cx="103" cy="32" r="7" fill="#fff" stroke="#c3c8d6" stroke-width="1"/>
    </svg>
    <div class="bookmark__content">
      <p class="abs brand brand--dental" style="top:170px">Harbourline Dental<br>Kelvale</p>
      <p class="abs contact" style="top:245px"><span class="contact__phone" style="display:block">Phone#: (02) 9000-3184</span></p>
      <div class="abs brand brand--clinic" style="top:300px"><span class="brand__mark"></span>Kelvale Clinic</div>
      <p class="abs contact" style="top:399px"><span class="contact__phone" style="display:block">Phone#: (02) 9000-3184</span></p>
      <p class="abs contact contact__address" style="top:449px;padding:0 26px">Address:<br><strong>14 Tamsin Crescent<br>WARRANGI, New South Wales(NSW), 2790</strong></p>
    </div>
  </section>

</main>
</body>
</html>
```